Business Card for Fashion House

We need a business card design for our personalize fashion service for our customers. the business card should reflect reliability, luxury and creativity.
The brand Gravetto is extracted from "Graceful Velvetto"; Gravetto provides fashion designs sprinkled with luxury and style tailored for our elite clients character profile.
Gravetto is created for those who embody class and elegance with a passion for style.
Target Market(s)
Affluent Customers
Industry/Entity Type
Fashion
Contact Information for Business Card
Samira Haddadin
Fashion Designer
Telephone: +971 4 555 0192
Mobile +971 50 555 0147
Emal info@gravetto-example.com
Website www.gravetto-example.com
Social Media Youtube g+ Facebook Instagram Pin /gravetto
Font styles to use
Other font styles liked:
- Audrey provided
Look and feel
Each slider illustrates characteristics of the customer's brand and the style your logo design should communicate.

```html
<!DOCTYPE html>
<html lang="en">
<head>
<meta charset="utf-8">
<title>Gravetto Business Card</title>
<link rel="stylesheet" href="https://fonts.googleapis.com/css2?family=Marcellus&display=swap">
<style>
  :root {
    --backdrop: #161616;
    --card-black: #0b0b0b;
    --card-charcoal: #2c2729;
    --card-charcoal-deep: #1a1718;
    --ink-white: #f4f4f4;
    --ink-soft: #cfcfcf;
    --band-light: #ffffff;
    --band-shade: #bdbdbd;
  }
  * { margin: 0; padding: 0; box-sizing: border-box; }
  html, body {
    width: 1200px; height: 864px; overflow: hidden;
    background: var(--backdrop);
    font-family: "Marcellus", "Optima", serif;
  }
  .stage { position: relative; width: 1200px; height: 864px; }

  .card {
    position: absolute; width: 560px; height: 320px;
    border-radius: 4px; overflow: hidden;
    box-shadow: 0 18px 40px rgba(0,0,0,.6);
  }

  /* Back side */
  .card-back { left: 580px; top: 90px; background: var(--card-black); }
  .card-back .band {
    position: absolute; left: 0; right: 0; top: 118px; height: 86px;
    background: linear-gradient(90deg, var(--band-shade), var(--band-light) 40%, var(--band-light) 70%, #dcdcdc);
  }
  .card-back .brand {
    position: absolute; left: 0; right: 0; top: 134px;
    display: flex; flex-direction: column; align-items: center; gap: 8px;
    color: var(--card-black);
  }
  .brand-dot {
    width: 26px; height: 26px; border-radius: 50%;
    border: 2px solid currentColor;
  }
  .brand-name { font-size: 22px; letter-spacing: 9px; padding-left: 9px; }

  /* Front side */
  .card-front { left: 60px; top: 440px; background: var(--card-black); }
  .card-front .upper {
    position: absolute; left: 0; right: 0; top: 0; height: 176px;
    background: linear-gradient(180deg, var(--card-charcoal), var(--card-charcoal-deep));
  }
  .card-front .brand {
    position: absolute; left: 0; right: 0; top: 62px;
    display: flex; flex-direction: column; align-items: center; gap: 12px;
    color: var(--ink-white);
  }
  .card-front .rule {
    position: absolute; left: 0; right: 0; top: 176px; height: 4px;
    background: var(--ink-white);
  }
  .details {
    position: absolute; left: 0; right: 0; top: 206px;
    display: flex; justify-content: center; gap: 22px; color: var(--ink-white);
  }
  .person { text-align: right; padding-top: 6px; }
  .person-name { font-size: 16px; letter-spacing: 1px; text-transform: uppercase; }
  .person-role { font-size: 11px; color: var(--ink-soft); margin-top: 3px; }
  .divider { width: 1px; height: 86px; background: var(--ink-white); }
  .contacts { list-style: none; display: flex; flex-direction: column; gap: 5px; }
  .contacts li { display: flex; align-items: center; gap: 10px; font-size: 12.5px; letter-spacing: .5px; }
  .contacts svg { width: 13px; height: 13px; flex: none; }
  .contacts .web { font-size: 11px; }
</style>
</head>
<body>
<main class="stage">
  <section class="card card-back" aria-label="Card back">
    <div class="band"></div>
    <div class="brand">
      <span class="brand-dot"></span>
      <span class="brand-name">GRAVETTO</span>
    </div>
  </section>

  <section class="card card-front" aria-label="Card front">
    <div class="upper"></div>
    <div class="brand">
      <span class="brand-dot"></span>
      <span class="brand-name">GRAVETTO</span>
    </div>
    <div class="rule"></div>
    <div class="details">
      <div class="person">
        <p class="person-name">Samira Haddadin</p>
        <p class="person-role">Fashion Designer</p>
      </div>
      <div class="divider"></div>
      <ul class="contacts">
        <li>
          <svg viewBox="0 0 14 14" fill="none" stroke="#f4f4f4" stroke-width="1.1"><circle cx="7" cy="7" r="6.3"/><path d="M4 5.5c0-1 1-1.3 3-1.3s3 .3 3 1.3M4.5 9.5h5l-.6-2.5h-3.8z"/></svg>
          <span>+971 4 555 0192</span>
        </li>
        <li>
          <svg viewBox="0 0 14 14" fill="none" stroke="#f4f4f4" stroke-width="1.1"><circle cx="7" cy="7" r="6.3"/><rect x="5" y="3.5" width="4" height="7" rx=".6"/></svg>
          <span>+971 50 555 0147</span>
        </li>
        <li>
          <svg viewBox="0 0 14 14" fill="none" stroke="#f4f4f4" stroke-width="1.1"><circle cx="7" cy="7" r="6.3"/><rect x="3.8" y="4.8" width="6.4" height="4.4"/><path d="M3.8 4.8 7 7.3l3.2-2.5"/></svg>
          <span>info@gravetto-example.com</span>
        </li>
        <li>
          <svg viewBox="0 0 14 14" fill="none" stroke="#f4f4f4" stroke-width="1.1"><circle cx="7" cy="7" r="6.3"/><ellipse cx="7" cy="7" rx="2.6" ry="6.3"/><path d="M.7 7h12.6"/></svg>
          <span class="web">www.gravetto-example.com</span>
        </li>
      </ul>
    </div>
  </section>
</main>
</body>
</html>
```